Business Card Design

I'm a commercial general contractor remodel offices, hotels, health clubs and stores mostly San Francisco and the peninsula
the file I down loaded is kind of what I want I like the I beam with my company name in it, that would be fine with me but if you have better Idea will look at it you never know, I'm decided to give in and change my company name to how every one knows me, I have been in business since 1991, I like the I beam logo I included one of my old card from my old company for reference for you.

BROCK CONSTRUCTION (is my company name)
Warren Pelkey contractor, LIc 514387
3148 Larkspur Row, San Bruno, California 94071
mobile, (415) 736-4052
phone (650) 514-2087
Fax, (650) 514-2088
email, brock@brockconstruction.example

```html
<!DOCTYPE html>
<html lang="en">
<head>
<meta charset="utf-8">
<title>Brock Construction – Business Card</title>
<link rel="stylesheet" href="https://fonts.googleapis.com/css2?family=Bowlby+One+SC&family=Open+Sans:wght@400;600;700&display=swap">
<style>
  :root {
    --backdrop: #e9e6e1;
    --card-white: #ffffff;
    --navy: #0f2342;
    --ink-dark: #111318;
    --accent-blue: #5aa6dd;
    --text-light: #ffffff;
  }
  * { margin: 0; padding: 0; box-sizing: border-box; }
  html, body {
    width: 1200px;
    height: 900px;
    overflow: hidden;
    background: var(--backdrop);
    font-family: "Open Sans", Arial, sans-serif;
  }
  .business-card {
    position: absolute;
    left: 75px;
    top: 150px;
    width: 1050px;
    height: 600px;
    background: var(--card-white);
    overflow: hidden;
    box-shadow: 0 10px 30px rgba(0,0,0,0.18);
  }
  .navy-field {
    position: absolute;
    inset: 0;
    width: 100%;
    height: 100%;
  }
  .company-title {
    position: absolute;
    top: 38px;
    left: 0;
    width: 100%;
    text-align: center;
    font-family: "Bowlby One SC", "Arial Black", sans-serif;
    font-size: 58px;
    letter-spacing: 1px;
    color: var(--ink-dark);
  }
  .brand-mark {
    position: absolute;
    top: 185px;
    left: 0;
    width: 100%;
    display: flex;
    justify-content: center;
    align-items: center;
    gap: 18px;
  }
  .brand-mark__square {
    width: 40px;
    height: 40px;
    background: var(--accent-blue);
  }
  .brand-mark__name {
    font-weight: 700;
    font-size: 56px;
    color: var(--accent-blue);
    letter-spacing: 2px;
  }
  .holder {
    position: absolute;
    top: 318px;
    left: 0;
    width: 100%;
    text-align: center;
  }
  .holder__name {
    font-size: 30px;
    font-weight: 400;
    color: var(--accent-blue);
    letter-spacing: 1px;
    text-transform: uppercase;
  }
  .holder__role {
    font-size: 17px;
    color: var(--accent-blue);
    margin-top: 2px;
  }
  .licence {
    position: absolute;
    top: 358px;
    right: 42px;
    font-size: 21px;
    color: var(--accent-blue);
  }
  .contact {
    position: absolute;
    bottom: 38px;
    font-size: 22px;
    line-height: 1.75;
    color: var(--text-light);
    font-weight: 600;
  }
  .contact--left { left: 42px; }
  .contact--right { right: 42px; text-align: right; }
</style>
</head>
<body>
  <main class="business-card">
    <svg class="navy-field" viewBox="0 0 1050 600" preserveAspectRatio="none" aria-hidden="true">
      <path d="M0 240 Q 520 70 1050 130 L1050 600 L0 600 Z" fill="var(--navy)"/>
    </svg>

    <h1 class="company-title">Brock Construction</h1>

    <div class="brand-mark">
      <span class="brand-mark__square"></span>
      <span class="brand-mark__name">BROCK CO.</span>
    </div>

    <div class="holder">
      <p class="holder__name">Warren Pelkey</p>
      <p class="holder__role">Contractor</p>
    </div>

    <p class="licence">Lic #514387</p>

    <div class="contact contact--left">
      <p>Fax : (650) 514-2088</p>
      <p>Email : brock@brockconstruction.example</p>
      <p>www.brockconstruction.example</p>
    </div>

    <div class="contact contact--right">
      <p>Cell : (415) 736-4052</p>
      <p>Telephone : (650) 514-2087</p>
      <p>Address : 3148 Larkspur Row San Bruno, Ca 94071</p>
    </div>
  </main>
</body>
</html>
```